Business card for marketing analytics company

Need a business card for new company. I have a logo already that I want to be built into the card and should use those colours

Company is called steered by tallies
Design must bring steered by tallies to life not be a card that could be for anyone with a logo put on it.

Like the front to be fairly clean and uncluttered bringing the logo out with a suitable design on the back of the card.

The logo represents a compass and business growth so those themes along with numbers, analytics , data are appropriate.
I'm often working with creative industries so also needs to reflect the creative side of analytics rather than be very corporate looking.

Target Market(s)

Ad agency, media agency, consumer goods clients

Industry/Entity Type

Market Research

Contact Information for Business Card

Needs to include name, title, email and phone number

Colors
f78f20
f68d4d
ec1f27

Requirements
Must have
• Must bring steered by tallies to life not be a card that could be for anyone with a logo put on it.
• Logo, Correct colours
• Like a design on the back that relates to company name
• Designs for both sides
Should not have
• Please do not just submit logo and a coloured card.
• It needs to have a design element to it
• No black background
• No clear cards - needs front & back

```html
<!DOCTYPE html>
<html lang="en">
<head>
<meta charset="utf-8">
<title>Steered by Tallies – Business Card</title>
<link rel="stylesheet" href="https://fonts.googleapis.com/css2?family=Source+Sans+3:wght@400;600;700&display=swap">
<style>
  :root {
    --backdrop: #b3b3b3;
    --card-front: #e8e8e8;
    --card-back: #f37324;
    --brand-red: #c1272d;
    --brand-orange: #f37324;
    --ink-light: #ffffff;
  }
  * { margin: 0; padding: 0; box-sizing: border-box; }
  html, body {
    width: 1200px;
    height: 900px;
    overflow: hidden;
    background: var(--backdrop);
    font-family: "Source Sans 3", "Myriad Pro", Arial, sans-serif;
  }
  .canvas { position: relative; width: 1200px; height: 900px; }
  .card {
    position: absolute;
    top: 215px;
    width: 414px;
    height: 414px;
    border-radius: 50%;
    overflow: hidden;
  }
  .card--front { left: 164px; background: var(--card-front); }
  .card--back  { left: 623px; background: var(--card-back); color: var(--ink-light); }

  .compass-dial {
    position: absolute;
    inset: 0;
    width: 414px;
    height: 414px;
  }
  .compass-dial--front { stroke: var(--brand-red); opacity: 0.35; }
  .compass-dial--back  { stroke: var(--ink-light); opacity: 0.3; }

  .front-mark {
    position: absolute;
    top: 150px;
    left: 0;
    width: 100%;
    text-align: center;
  }
  .front-mark__name {
    color: var(--brand-red);
    font-weight: 600;
    font-size: 44px;
    line-height: 1.05;
  }
  .growth-bars {
    display: block;
    margin: 22px auto 0;
  }
  .growth-bars rect:nth-child(odd)  { fill: var(--brand-orange); }
  .growth-bars rect:nth-child(even) { fill: var(--brand-red); }

  .holder {
    position: absolute;
    top: 69px;
    left: 0;
    width: 100%;
    text-align: center;
  }
  .holder__name { font-weight: 700; font-size: 20px; line-height: 24px; letter-spacing: 0.2px; }
  .holder__title { font-weight: 400; font-size: 18px; line-height: 22px; }

  .brand {
    position: absolute;
    top: 162px;
    left: 42px;
    display: flex;
    align-items: center;
    gap: 22px;
  }
  .brand__dot {
    width: 100px;
    height: 100px;
    border-radius: 50%;
    border: 3px solid var(--ink-light);
    flex: none;
  }
  .brand__name {
    font-weight: 600;
    font-size: 32px;
    line-height: 32px;
  }
  .brand__line { display: block; }
  .brand__line--indent { padding-left: 46px; }

  .contact {
    position: absolute;
    top: 292px;
    left: 0;
    width: 100%;
    text-align: center;
    font-size: 18px;
    line-height: 28px;
  }
  .contact__icons {
    display: flex;
    justify-content: center;
    gap: 8px;
    height: 20px;
    margin-bottom: 6px;
  }
  .contact__icons svg { fill: var(--ink-light); }
</style>
</head>
<body>
<main class="canvas">
  <section class="card card--front">
    <svg class="compass-dial compass-dial--front" viewBox="0 0 414 414" aria-hidden="true">
      <circle cx="207" cy="207" r="188" fill="none" stroke-width="10" stroke-dasharray="1.5 14.9"/>
      <circle cx="207" cy="207" r="176" fill="none" stroke-width="1"/>
    </svg>
    <div class="front-mark">
      <p class="front-mark__name">Steered<br>by Tallies</p>
      <svg class="growth-bars" width="74" height="36" viewBox="0 0 74 36" aria-hidden="true">
        <rect x="0"  y="26" width="10" height="10"/>
        <rect x="16" y="19" width="10" height="17"/>
        <rect x="32" y="13" width="10" height="23"/>
        <rect x="48" y="6"  width="10" height="30"/>
        <rect x="64" y="0"  width="10" height="36"/>
      </svg>
    </div>
  </section>

  <section class="card card--back">
    <svg class="compass-dial compass-dial--back" viewBox="0 0 414 414" aria-hidden="true">
      <circle cx="207" cy="207" r="196" fill="none" stroke-width="8" stroke-dasharray="1.5 15.6"/>
    </svg>
    <div class="holder">
      <p class="holder__name">MARCUS ELLERY</p>
      <p class="holder__title">Managing Director</p>
    </div>

    <div class="brand">
      <span class="brand__dot"></span>
      <p class="brand__name">
        <span class="brand__line">Steered by</span>
        <span class="brand__line brand__line--indent">Tallies</span>
      </p>
    </div>

    <div class="contact">
      <div class="contact__icons">
        <svg width="16" height="18" viewBox="0 0 24 24" aria-hidden="true">
          <path d="M6.6 10.8c1.4 2.8 3.8 5.1 6.6 6.6l2.2-2.2c.3-.3.7-.4 1-.2 1.1.4 2.3.6 3.6.6.6 0 1 .4 1 1V20c0 .6-.4 1-1 1C10.6 21 3 13.4 3 4c0-.6.4-1 1-1h3.5c.6 0 1 .4 1 1 0 1.3.2 2.5.6 3.6.1.3 0 .7-.2 1z"/>
        </svg>
        <svg width="22" height="18" viewBox="0 0 22 16" aria-hidden="true">
          <path d="M0 0h22v16H0z M2 2v.4l9 6 9-6V2z M2 4.8V14h18V4.8l-9 6z" fill-rule="evenodd"/>
        </svg>
      </div>
      <p class="contact__phone">712-4830-000</p>
      <p class="contact__email">hello@tallybook.com</p>
    </div>
  </section>
</main>
</body>
</html>
```